Business card design for Korvane Engineering Tandem

We need a new business card design along with all the necessary to place an order. The company is Korvane Engineering Tandem and we recently updated our logo.

```html
<!DOCTYPE html>
<html lang="en">
<head>
<meta charset="utf-8">
<title>Korvane Engineering Tandem — Business Card</title>
<link href="https://fonts.googleapis.com/css2?family=Montserrat:wght@500;600&family=Nunito+Sans:wght@400;600;700&display=swap" rel="stylesheet">
<style>
  :root {
    --backdrop: #1b1a1e;
    --card: #232527;
    --card-shade: #1e2022;
    --steel: #8f8e8b;
    --steel-light: #a3a2a0;
    --gold: #e6c01f;
    --shadow: rgba(0, 0, 0, 0.55);
  }
  * { box-sizing: border-box; margin: 0; padding: 0; }
  html, body {
    width: 1200px;
    height: 801px;
    overflow: hidden;
    background: var(--backdrop);
  }
  .sheet {
    width: 1200px;
    height: 801px;
    display: flex;
    align-items: center;
    justify-content: center;
    gap: 40px;
  }
  .card {
    position: relative;
    width: 540px;
    height: 309px;
    background: linear-gradient(150deg, var(--card) 0%, var(--card) 55%, var(--card-shade) 100%);
    box-shadow: 0 18px 40px var(--shadow);
    overflow: hidden;
  }
  .brand {
    display: flex;
    align-items: center;
    gap: 12px;
    font-family: "Montserrat", sans-serif;
    font-weight: 600;
    color: var(--steel);
  }
  .brand-mark {
    width: 14px;
    height: 14px;
    background: var(--gold);
    flex: none;
  }
  .brand-name {
    line-height: 1.15;
    text-transform: uppercase;
  }
  .brand-name .primary { display: block; font-size: 40px; letter-spacing: 0.06em; }
  .brand-name .secondary { display: block; font-size: 13px; letter-spacing: 0.14em; }

  .card--front .brand {
    position: absolute;
    left: 50%;
    top: 50%;
    transform: translate(-50%, -50%);
  }

  .card--back .brand {
    position: absolute;
    left: 34px;
    top: 58%;
    transform: translateY(-50%);
  }
  .card--back .brand-name .primary { font-size: 31px; }
  .card--back .brand-name .secondary { font-size: 10.5px; letter-spacing: 0.12em; }

  .divider {
    position: absolute;
    left: 300px;
    top: 70px;
    width: 1px;
    height: 170px;
    background: var(--gold);
  }
  .contact {
    position: absolute;
    left: 322px;
    top: 72px;
    font-family: "Nunito Sans", sans-serif;
    color: var(--steel-light);
    font-size: 12.5px;
    line-height: 1.5;
  }
  .contact-name {
    font-weight: 700;
    font-size: 15px;
    letter-spacing: 0.03em;
    text-transform: uppercase;
  }
  .contact-role {
    color: var(--gold);
    font-weight: 600;
    font-size: 13px;
    margin-bottom: 14px;
  }
  .contact-address { margin-bottom: 12px; }
  .contact-line {
    display: flex;
    align-items: center;
    gap: 8px;
  }
  .contact-line svg { flex: none; }
</style>
</head>
<body>
<main class="sheet">
  <section class="card card--front" aria-label="Card front">
    <div class="brand">
      <span class="brand-mark"></span>
      <span class="brand-name">
        <span class="primary">Korvane</span>
        <span class="secondary">Engineering Tandem</span>
      </span>
    </div>
  </section>

  <section class="card card--back" aria-label="Card back">
    <div class="brand">
      <span class="brand-mark"></span>
      <span class="brand-name">
        <span class="primary">Korvane</span>
        <span class="secondary">Engineering Tandem</span>
      </span>
    </div>
    <span class="divider"></span>
    <div class="contact">
      <p class="contact-name">Noel R. Hart</p>
      <p class="contact-role">Partner</p>
      <p class="contact-address">Level 3, 48 Harbour Lane<br>Sydney NSW 2000</p>
      <p class="contact-line">
        <svg width="12" height="12" viewBox="0 0 12 12" aria-hidden="true"><rect x="1.5" y="1.5" width="9" height="9" rx="1" fill="none" stroke="var(--gold)" stroke-width="1.6"/></svg>
        0198 765 432
      </p>
      <p class="contact-line">
        <svg width="12" height="12" viewBox="0 0 12 12" aria-hidden="true"><rect x="1" y="2.5" width="10" height="7" fill="var(--gold)"/><path d="M1 2.5 L6 6.5 L11 2.5" fill="none" stroke="var(--card)" stroke-width="1"/></svg>
        info@korvanetandem.co
      </p>
    </div>
  </section>
</main>
</body>
</html>
```